Website for IT consulting Company

I need a website upgrade, the existing site content is ok, I would also like to add a testimonial page, the site should be something that is easy for us to update content. You use the content from www.kelvanbrook.com as an example. I will also post update logo and artwork. I also need a contact form with some type of validation or captcha.

I added Coded to the Project

Please omit Address maps

Target Market(s)

small business, service oriented companies. We provide IT Consulting, support and mangement

Industry/Entity Type

Information Technology

Coding

Number of Pages Required

1 page

Font styles to use
Serif
Sans Serif

Requirements
Must have
• Contain logo attached, and content from existing web site www.kelvanbrook.com.
• Also need to update content easily, and be movable to different platforms.
• There is a catch phrase
• "Let us worry about your technology…” “ so you don’t have to!”
• Should be included.
Nice to have
• Testimonial page, Project page where we can post new and past projects and pictures
Should not have
• none

```html
<!DOCTYPE html>
<html lang="en">
<head>
<meta charset="utf-8">
<title>Kelvanbrook Technology Group – IT Consulting</title>
<link href="https://fonts.googleapis.com/css2?family=Exo+2:ital,wght@0,600;0,700;0,800;1,700;1,800&family=Arimo:wght@400;700&family=Tinos&display=swap" rel="stylesheet">
<style>
:root{
  --blue:#1b8fd6;
  --blue-dark:#0f6fb3;
  --blue-light:#3fb0ec;
  --black:#050505;
  --ink:#1c1c1c;
  --gray-bg:#e9e9e9;
  --gray-mid:#8d8d8d;
  --footer:#2a2a2c;
  --white:#ffffff;
}
*{margin:0;padding:0;box-sizing:border-box}
html,body{width:1200px;height:2557px;overflow:hidden}
body{position:relative;background:var(--white);font-family:"Arimo",Arial,sans-serif;color:var(--ink)}
.abs{position:absolute}
.display{font-family:"Exo 2",Arial,sans-serif;font-weight:800;font-style:italic}

/* header */
.site-header{left:0;top:0;width:1200px;height:125px;background:var(--black)}
.brand{left:82px;top:34px;display:flex;align-items:center;gap:14px}
.brand-mark{width:40px;height:40px;background:var(--blue);border-radius:6px}
.brand-name{font-family:"Exo 2",sans-serif;font-weight:700;font-size:50px;color:var(--white);letter-spacing:1px}
.follow{right:98px;top:16px;display:flex;align-items:center;gap:8px;color:var(--white);font-size:17px}
.follow .lbl{margin-right:6px}
.social-sq{width:26px;height:26px;background:#cfcfcf;border-radius:3px}
.contact-strip{right:84px;top:68px;display:flex;align-items:center;gap:14px;color:var(--white)}
.icon-box{width:40px;height:40px;background:var(--blue);border-radius:4px;display:flex;align-items:center;justify-content:center}
.contact-strip .phone{font-family:"Exo 2",sans-serif;font-weight:700;font-size:23px;margin-right:18px}
.contact-strip .support{font-family:"Exo 2",sans-serif;font-weight:800;font-size:20px}

/* nav */
.main-nav{left:0;top:125px;width:1200px;height:55px;background:linear-gradient(#2aa4e8,#1180c8)}
.main-nav a{position:absolute;top:14px;transform:translateX(-50%);font-size:20px;color:var(--white);text-decoration:none;letter-spacing:.5px}
.main-nav a.active{color:#1a2a38}

/* hero */
.hero{left:0;top:180px;width:1200px;height:534px;background:linear-gradient(180deg,#3b3444 0%,#5a4a58 30%,#3a3540 58%,#2a2a30 80%,#1f1f24 100%)}
.hero-name{left:0;width:1200px;top:330px;text-align:center;font-family:"Exo 2",sans-serif;font-weight:700;font-size:30px;color:var(--white);opacity:.95}
.hero-line1{left:0;width:1200px;top:470px;text-align:center;font-size:34px;color:var(--white)}
.hero-line2{left:0;width:1200px;top:518px;text-align:center;font-size:36px;color:var(--blue-light)}
.dots{left:570px;top:690px;display:flex;gap:5px}
.dots span{width:10px;height:10px;background:#8a8a8a}
.dots span.on{background:var(--white)}

/* welcome */
.welcome-title{left:0;width:1200px;top:758px;text-align:center;font-size:28px;color:var(--ink)}
.welcome-title em,.services-title em,.panel h3 em,.foot-col h4 em{color:var(--blue);font-style:inherit}
.rule{height:3px;background:var(--blue);width:78px;left:561px}
.welcome-text{left:85px;width:1030px;top:822px;text-align:center;font-size:14.5px;line-height:27px;color:#222}
.read-more{left:0;width:1200px;top:916px;text-align:center;font-family:"Exo 2",sans-serif;font-weight:800;font-style:italic;font-size:15px;color:var(--blue-dark);text-decoration:underline}

/* services */
.services{left:0;top:978px;width:1200px;height:575px;background:var(--gray-bg)}
.services-title{left:0;width:1200px;top:1022px;text-align:center;font-size:30px;color:var(--ink)}
.service-label{font-family:"Exo 2",sans-serif;font-weight:800;font-style:italic;font-size:17px;fill:#222}

/* panels */
.panel{top:1553px;height:387px;width:600px}
.panel-support{left:0;background:linear-gradient(180deg,#2ea2e6,#1477c0)}
.panel-outsource{left:600px;background:linear-gradient(180deg,#b5b5b5,#6f6f71)}
.panel h3{position:absolute;top:62px;font-size:25px;color:var(--white);display:flex;align-items:center;gap:12px}
.panel h3 .glyph{width:30px;height:34px}
.panel .divider{position:absolute;top:108px;height:1px;width:495px;background:rgba(255,255,255,.35)}
.panel .photo{position:absolute;top:130px;width:205px;height:185px;border:2px solid rgba(255,255,255,.5)}
.panel p{position:absolute;top:127px;width:255px;font-size:14.5px;line-height:26px;color:var(--white)}
.btn-more{position:absolute;top:277px;width:152px;height:38px;font-family:"Tinos",serif;font-size:18px;color:var(--white);display:flex;align-items:center;justify-content:center;gap:10px}
.panel-support .btn-more{background:linear-gradient(#a7a7a7,#7a7a7a)}
.panel-outsource .btn-more{background:linear-gradient(#2aa4e8,#1180c8)}
.notch{left:560px;top:1553px;width:0;height:0;border-left:40px solid transparent;border-right:40px solid transparent;border-top:38px solid var(--gray-bg)}

/* call to action */
.cta-title{left:0;width:1200px;top:1978px;text-align:center;font-size:36px;color:#111}
.cta-sub{left:0;width:1200px;top:2025px;text-align:center;font-size:30px;color:#111}
.cta-btn{left:472px;top:2088px;display:flex;align-items:center;gap:8px}
.cta-pill{height:48px;width:200px;border-radius:6px;background:linear-gradient(#9a9a9a,#5e5e5e);color:var(--white);font-family:"Exo 2",sans-serif;font-weight:800;font-style:italic;display:flex;align-items:center;gap:8px;padding-left:8px;line-height:19px;font-size:17px}
.cta-square{width:44px;height:44px;background:var(--blue);border-radius:6px}

/* footer */
.site-footer{left:0;top:2185px;width:1200px;height:327px;background:linear-gradient(180deg,#3a3a3d,#232326)}
.foot-col{top:2240px}
.foot-col h4{font-family:"Exo 2",sans-serif;font-weight:800;font-style:italic;font-size:19px;color:var(--white);padding-bottom:10px;border-bottom:1px solid rgba(255,255,255,.2);width:135px}
.foot-col ul{list-style:none;margin-top:12px}
.quick li{font-size:14px;color:#e8e8e8;height:25px;padding-left:18px;position:relative}
.quick li::before{content:"";position:absolute;left:0;top:6px;width:4px;height:4px;border-radius:50%;background:var(--blue-light)}
.contact-col p{font-size:14.5px;color:#e8e8e8;line-height:21px}
.contact-col .row{display:flex;align-items:center;gap:10px;font-size:14px;color:#e8e8e8;margin-top:14px}
.social-list li{display:flex;align-items:center;gap:14px;font-size:14px;color:#e8e8e8;height:44px}
.social-list .sq{width:30px;height:30px;background:#d9d9d9;border-radius:3px}
.foot-brand{left:880px;top:2290px;display:flex;align-items:center;gap:16px}
.foot-brand .sq{width:90px;height:90px;background:var(--blue);border-radius:12px;opacity:.9}
.foot-brand .nm{font-family:"Exo 2",sans-serif;font-weight:700;font-size:34px;color:var(--white);opacity:.85}
.copyright{left:0;top:2512px;width:1200px;height:45px;background:linear-gradient(#2aa4e8,#1180c8);color:var(--white);font-size:15px;text-align:center;line-height:45px}
</style>
</head>
<body>

<header class="site-header abs">
  <div class="brand abs"><span class="brand-mark"></span><span class="brand-name">Kelvanbrook</span></div>
  <div class="follow abs"><span class="lbl display">Follow Us On</span><span class="social-sq"></span><span class="social-sq"></span><span class="social-sq"></span><span class="social-sq"></span></div>
  <div class="contact-strip abs">
    <span class="icon-box"><svg width="22" height="22" viewBox="0 0 24 24"><path d="M6.6 10.8c1.4 2.8 3.8 5.1 6.6 6.6l2.2-2.2c.3-.3.7-.4 1-.2 1.1.4 2.3.6 3.6.6.6 0 1 .4 1 1V20c0 .6-.4 1-1 1C10.6 21 3 13.4 3 4c0-.6.4-1 1-1h3.5c.6 0 1 .4 1 1 0 1.3.2 2.5.6 3.6.1.3 0 .7-.2 1z" fill="#fff"/></svg></span>
    <span class="phone">(555) 014-2287</span>
    <span class="icon-box"><svg width="22" height="22" viewBox="0 0 24 24"><circle cx="12" cy="8" r="4.5" fill="#fff"/><path d="M3 21c0-5 4-8 9-8s9 3 9 8z" fill="#fff"/></svg></span>
    <span class="support">SUPPORT</span>
  </div>
</header>

<nav class="main-nav abs display">
  <a class="active" style="left:126px">HOME</a>
  <a style="left:298px">ABOUT US</a>
  <a style="left:489px">SERVICES</a>
  <a style="left:672px">CLIENTS</a>
  <a style="left:851px">CAREERS</a>
  <a style="left:1052px">CONTACT US</a>
</nav>

<section class="hero abs" role="img" aria-label="Night skyline of a city with lit highways at dusk"></section>
<div class="hero-name abs">Kelvanbrook</div>
<div class="hero-line1 abs display">Let Us Worry About Your Technology...</div>
<div class="hero-line2 abs display">So You Don't Have To!</div>
<div class="dots abs"><span></span><span></span><span></span><span class="on"></span></div>

<h1 class="welcome-title abs display">WELCOME TO KELVANBROOK <em>TECHNOLOGY GROUP, INC</em></h1>
<div class="rule abs" style="top:798px"></div>
<p class="welcome-text abs">Kelvanbrook Technology Group, Inc. was established in 1991. Our mission is helping businesses and individuals realize a Return on Investment by implementing today's advanced technologies. As a small business we understand the importance of technology and personalized attention.&nbsp; Every member of our support team has worked with both large and small companies supporting a multitude of applications, networks and environments.</p>
<div class="read-more abs">READ MORE</div>

<section class="services abs">
  <svg class="abs" style="left:0;top:0" width="1200" height="575" viewBox="0 978 1200 575">
    <g stroke="#9a9a9a" stroke-width="2" stroke-dasharray="2 5" fill="none">
      <line x1="377" y1="1462" x2="323" y2="1462"/>
      <line x1="410" y1="1355" x2="365" y2="1350"/>
      <line x1="462" y1="1304" x2="425" y2="1290"/>
      <line x1="533" y1="1260" x2="509" y2="1245"/>
      <line x1="615" y1="1245" x2="615" y2="1223"/>
      <line x1="697" y1="1260" x2="722" y2="1246"/>
      <line x1="765" y1="1302" x2="805" y2="1290"/>
      <line x1="820" y1="1355" x2="866" y2="1352"/>
      <line x1="830" y1="1462" x2="908" y2="1462"/>
    </g>
    <circle cx="604" cy="1462" r="229" fill="#fff" stroke="#8c8c8c" stroke-width="9"/>
    <rect x="0" y="1553" width="1200" height="10" fill="#fff"/>
    <g fill="#fff" stroke="#8c8c8c" stroke-width="3">
      <circle cx="377" cy="1462" r="8"/><circle cx="410" cy="1355" r="8"/><circle cx="462" cy="1304" r="8"/>
      <circle cx="533" cy="1260" r="8"/><circle cx="615" cy="1234" r="8"/><circle cx="697" cy="1260" r="8"/>
      <circle cx="765" cy="1302" r="8"/><circle cx="820" cy="1355" r="8"/><circle cx="830" cy="1462" r="8"/>
    </g>
    <g fill="#1a8ad2" stroke="#fff" stroke-width="4">
      <circle cx="273" cy="1462" r="50"/><circle cx="315" cy="1350" r="50"/><circle cx="394" cy="1261" r="50"/>
      <circle cx="499" cy="1200" r="50"/><circle cx="615" cy="1173" r="50"/><circle cx="733" cy="1202" r="50"/>
      <circle cx="837" cy="1261" r="50"/><circle cx="915" cy="1352" r="50"/><circle cx="958" cy="1462" r="50"/>
    </g>
    <g fill="none" stroke="#fff" stroke-width="3" stroke-linecap="round" stroke-linejoin="round">
      <rect x="253" y="1446" width="40" height="26" rx="2"/><line x1="247" y1="1478" x2="299" y2="1478"/>
      <circle cx="308" cy="1342" r="8"/><path d="M294 1368c0-9 6-14 14-14s14 5 14 14"/><rect x="320" y="1348" width="16" height="12"/>
      <path d="M394 1250v32M386 1284l8-24 8 24M380 1248a16 16 0 0 0 0 20M408 1248a16 16 0 0 1 0 20"/>
      <circle cx="499" cy="1200" r="20"/><line x1="493" y1="1191" x2="493" y2="1209"/><line x1="505" y1="1191" x2="505" y2="1209"/>
      <rect x="597" y="1156" width="36" height="12" rx="3"/><rect x="597" y="1172" width="36" height="12" rx="3"/><rect x="597" y="1188" width="36" height="10" rx="3"/>
      <rect x="713" y="1186" width="30" height="22" rx="2"/><rect x="745" y="1194" width="12" height="20" rx="2"/><line x1="722" y1="1214" x2="736" y2="1214"/>
      <path d="M820 1272l22-22 12 12-22 22zM818 1276l-6 6"/>
      <path d="M897 1362h36v10h-36zM902 1350a18 18 0 0 1 26 0M896 1342a27 27 0 0 1 38 0"/>
      <path d="M958 1438l20 7v14c0 12-9 20-20 25-11-5-20-13-20-25v-14z"/>
    </g>
    <text class="service-label" x="228" y="1460" text-anchor="end">DESKTOP</text>
    <text class="service-label" x="205" y="1479" text-anchor="end">SUPPORT</text>
    <text class="service-label" x="250" y="1337" text-anchor="end">NETWORK</text>
    <text class="service-label" x="250" y="1354" text-anchor="end">ADMINISTRATION</text>
    <text class="service-label" x="328" y="1252" text-anchor="end">TELECOMMUNICATIONS</text>
    <text class="service-label" x="447" y="1176" text-anchor="end">AUDIO/VIDEO MULTIMEDIA</text>
    <text class="service-label" x="620" y="1119" text-anchor="middle">DISASTER RECOVERY</text>
    <text class="service-label" x="782" y="1167">WEB DESIGN</text>
    <text class="service-label" x="900" y="1253">NETWORK CABLING</text>
    <text class="service-label" x="982" y="1344">WIRELESS</text>
    <text class="service-label" x="982" y="1362">NETWORKS</text>
    <text class="service-label" x="1016" y="1456">ANTIVIRUS</text>
    <text class="service-label" x="1016" y="1473">SOLUTIONS</text>
    <rect x="534" y="1372" width="50" height="50" rx="8" fill="#1a8ad2"/>
    <text x="604" y="1508" text-anchor="middle" font-family="'Exo 2',sans-serif" font-weight="700" font-size="46" fill="#7a7a7a">Kelvanbrook</text>
  </svg>
</section>
<h2 class="services-title abs display">OUR <em>SERVICES</em></h2>
<div class="rule abs" style="top:1060px;width:56px;left:578px"></div>

<section class="panel panel-support abs">
  <h3 class="display" style="left:85px"><svg class="glyph" viewBox="0 0 30 34"><circle cx="15" cy="9" r="7" fill="none" stroke="#fff" stroke-width="2.5"/><path d="M2 33c0-8 6-13 13-13s13 5 13 13z" fill="#fff"/></svg>IT SUPPORT SOLUTIONS</h3>
  <div class="divider" style="left:85px"></div>
  <div class="photo" role="img" aria-label="Technicians inspecting server racks in a data center" style="left:85px;background:linear-gradient(135deg,#3d5f86,#9fb6cc 55,#2b3e58)"></div>
  <p style="left:310px">Lorem ipsum dolor sit amet, consecretk etuer adipiscing elit, sed diam nonumre my nibh euismod tinciduntol ut laoret et re olore magna aliquam erat volutpt. Ut wisi minim consequat.</p>
  <div class="btn-more" style="left:310px">Read More <span>&#10230;</span></div>
</section>
<section class="panel panel-outsource abs">
  <h3 class="display" style="left:36px;color:#111"><svg class="glyph" viewBox="0 0 30 34"><circle cx="15" cy="8" r="5" fill="#111"/><path d="M6 22c0-5 4-8 9-8s9 3 9 8z" fill="#111"/><rect x="1" y="24" width="28" height="3" fill="#111"/><line x1="5" y1="27" x2="5" y2="34" stroke="#111" stroke-width="2"/><line x1="25" y1="27" x2="25" y2="34" stroke="#111" stroke-width="2"/></svg>WHY OUTSOURCE TECHNOLOGIES</h3>
  <div class="divider" style="left:36px"></div>
  <div class="photo" role="img" aria-label="Hand holding a glowing globe surrounded by floating screens" style="left:36px;background:radial-gradient(circle at 50% 45%,#cfe6f7,#3b6c97 45%,#0d1e33)"></div>
  <p style="left:258px">Lorem ipsum dolor sit amet, consecretk etuer adipiscing elit, sed diam nonumre my nibh euismod tinciduntol ut laoret et re olore magna aliquam erat volutpt. Ut wisi minim consequat.</p>
  <div class="btn-more" style="left:258px">Read More <span>&#10230;</span></div>
</section>
<div class="notch abs"></div>

<h2 class="cta-title abs display">IT Solutions That Works For Your Business</h2>
<div class="cta-sub abs display">A Full Service Technology Company</div>
<div class="cta-btn abs">
  <div class="cta-pill"><svg width="24" height="24" viewBox="0 0 24 24"><path d="M6.6 10.8c1.4 2.8 3.8 5.1 6.6 6.6l2.2-2.2c.3-.3.7-.4 1-.2 1.1.4 2.3.6 3.6.6.6 0 1 .4 1 1V20c0 .6-.4 1-1 1C10.6 21 3 13.4 3 4c0-.6.4-1 1-1h3.5c.6 0 1 .4 1 1 0 1.3.2 2.5.6 3.6.1.3 0 .7-.2 1z" fill="#fff"/></svg><span>Call Us Today<br>(555) 014-2287</span></div>
  <span class="cta-square"></span>
</div>

<footer class="site-footer abs" role="img" aria-label="Faded night city skyline behind footer"></footer>
<div class="foot-col quick abs" style="left:85px">
  <h4>Quick <em>Links</em></h4>
  <ul><li>Home</li><li>About Us</li><li>Services</li><li>Support</li><li>Clients</li><li>Careers</li><li>Contact Us</li></ul>
</div>
<div class="foot-col contact-col abs" style="left:318px">
  <h4 style="width:190px">Contact <em>Details</em></h4>
  <p style="margin-top:10px">Kelvanbrook Technology Group, Inc.</p>
  <p style="margin-top:10px">418 Marlow Ave.<br>Fairhaven, Ohio 45210</p>
  <div class="row"><svg width="14" height="14" viewBox="0 0 24 24"><path d="M6.6 10.8c1.4 2.8 3.8 5.1 6.6 6.6l2.2-2.2c.3-.3.7-.4 1-.2 1.1.4 2.3.6 3.6.6.6 0 1 .4 1 1V20c0 .6-.4 1-1 1C10.6 21 3 13.4 3 4c0-.6.4-1 1-1h3.5c.6 0 1 .4 1 1 0 1.3.2 2.5.6 3.6.1.3 0 .7-.2 1z" fill="#3fb0ec"/></svg>(555) 014-2287</div>
  <div class="row"><svg width="14" height="14" viewBox="0 0 24 24"><rect x="5" y="2" width="14" height="6" fill="#3fb0ec"/><rect x="2" y="9" width="20" height="9" rx="2" fill="#3fb0ec"/><rect x="6" y="15" width="12" height="7" fill="#fff"/></svg>(555) 014-2287</div>
  <div class="row"><svg width="14" height="14" viewBox="0 0 24 24"><rect x="2" y="5" width="20" height="14" rx="2" fill="#3fb0ec"/><path d="M2 6l10 7 10-7" stroke="#fff" stroke-width="2" fill="none"/></svg>info@kelvanbrook.com</div>
</div>
<div class="foot-col abs" style="left:653px">
  <h4>Get <em>Social</em></h4>
  <ul class="social-list"><li><span class="sq"></span>Friendsphere</li><li><span class="sq"></span>Chirper</li><li><span class="sq"></span>Circlesphere</li><li><span class="sq"></span>ProNet</li></ul>
</div>
<div class="foot-brand abs"><span class="sq"></span><span class="nm">Kelvanbrook</span></div>
<div class="copyright abs">Copyright &copy; 2017 Kelvanbrook Technology Group, Inc. All Rights Reserved.</div>

</body>
</html>
```